Teach English in China Website Redesign Needed

We recruit native English speakers from the US, UK, etc. who want to teach English as a foreign language in schools in China. Our target customer is college educated, age 22-28 and they love to travel. We prefer designs with bright colors and lots of photos. We want to keep all the text on our current homepage, BrightLanternPost.com. We are open to changing our logo. A competitor's page that we like is pinemeadowtutors.com because of their bright colors, photos and use of white space. We are happy to give you a dofollow link and design credit on our homepage. The use of included photos is optional. We need at least a home page design and a standard blog post design.
Target Market(s)
Our target customer is college educated, age 22-28 and they love to travel. Half of our customers are kindergarten teachers. Half of our customers are male.
Logo Text
Bright Lantern Post
Requirements
Must have
- Bright colors
Should not have
- Our homepage must not look crowded. Use white space effectively.

```html
<!DOCTYPE html>
<html lang="en">
<head>
<meta charset="utf-8">
<title>Bright Lantern Post – Teach English in China</title>
<link href="https://fonts.googleapis.com/css2?family=Nunito+Sans:wght@400;600;700&family=Open+Sans:ital,wght@0,400;0,600;0,700;1,400;1,600&display=swap" rel="stylesheet">
<style>
:root{
  --red:#e8100f;
  --red-dark:#c40d0c;
  --ink:#222222;
  --text:#555555;
  --muted:#777777;
  --line:#dddddd;
  --white:#ffffff;
  --footer:#f4f4f4;
  --btn-dark:#555555;
}
*{margin:0;padding:0;box-sizing:border-box}
html,body{width:1200px;height:3529px;overflow:hidden;background:var(--white)}
body{position:relative;font-family:"Open Sans",sans-serif;color:var(--text)}
.abs{position:absolute}
.heading{font-family:"Nunito Sans",sans-serif;color:var(--ink);font-weight:400}

/* Header */
.site-header{position:absolute;left:0;top:0;width:1200px;height:106px;background:var(--white)}
.brand{position:absolute;left:134px;top:30px;display:flex;align-items:center;gap:10px;font-family:"Nunito Sans",sans-serif;font-weight:700;font-size:22px;color:var(--red);line-height:1}
.brand-dot{width:14px;height:14px;border-radius:50%;background:var(--red)}
.main-nav a{position:absolute;top:44px;font-family:"Nunito Sans",sans-serif;font-size:17px;font-weight:600;color:#444;text-decoration:none;letter-spacing:.5px}
.main-nav a.active{color:var(--red)}
.nav-marker{position:absolute;left:421px;top:0;width:62px;height:5px;background:var(--red)}

/* Hero */
.hero{position:absolute;left:0;top:106px;width:1200px;height:593px;background:linear-gradient(180deg,#1c2a6a 0%,#3a2a6e 30%,#8a1a1a 60%,#c8251a 80%,#7a1010 100%)}
.hero-title{position:absolute;left:98px;top:224px;font-family:"Nunito Sans",sans-serif;color:var(--white);text-transform:uppercase;line-height:1.3}
.hero-title .l1{display:block;font-size:44px;font-weight:700}
.hero-title .l2{display:block;font-size:36px;font-weight:600}
.btn-red{position:absolute;display:flex;align-items:center;justify-content:center;background:var(--red);color:var(--white);font-family:"Nunito Sans",sans-serif;font-weight:700;font-size:16px;text-transform:uppercase;letter-spacing:.5px}
.hero-dots{position:absolute;left:564px;top:557px;display:flex;gap:8px}
.hero-dots span{width:13px;height:13px;border-radius:50%;border:2px solid var(--white)}
.hero-dots span.on{background:var(--white)}

/* What we do */
.what-we-do{position:absolute;left:0;top:699px;width:1200px;height:453px;background:linear-gradient(180deg,#ffffff 60%,#f0f0f0 100%)}
.section-title{font-family:"Nunito Sans",sans-serif;color:var(--ink);font-size:32px;font-weight:400}
.body-copy{font-size:14px;line-height:25px;color:var(--text)}
.btn-tab{clip-path:polygon(0 0,88% 0,100% 100%,0 100%)}

/* Cards */
.card{position:absolute;top:1223px;width:309px;height:422px;background:var(--white);box-shadow:0 4px 14px rgba(0,0,0,.14)}
.card-photo{width:309px;height:205px}
.card h3{position:absolute;left:28px;top:228px;font-family:"Nunito Sans",sans-serif;font-weight:400;font-size:23px;color:var(--red)}
.card p{position:absolute;left:28px;top:268px;width:255px;font-size:11.5px;line-height:18px;color:var(--muted)}
.btn-small{position:absolute;left:28px;top:353px;width:140px;height:35px;background:var(--btn-dark);color:var(--white);font-family:"Nunito Sans",sans-serif;font-weight:700;font-size:11px;display:flex;align-items:center;justify-content:center;padding-right:16px;clip-path:polygon(0 0,85% 0,100% 100%,0 100%)}

/* Testimonials */
.testimonials{position:absolute;left:0;top:1716px;width:1200px;height:415px;background:var(--red)}
.testimonials h2{position:absolute;left:0;width:1200px;top:42px;text-align:center;font-family:"Nunito Sans",sans-serif;font-weight:600;font-size:34px;color:var(--white)}
.quote-pill{position:absolute;left:290px;top:130px;width:620px;height:200px;border-radius:100px;background:var(--red-dark);opacity:.55}
.quote-badge{position:absolute;left:566px;top:100px;width:62px;height:62px;border-radius:50%;background:var(--white);display:flex;align-items:center;justify-content:center;font-family:Georgia,serif;font-size:50px;line-height:1;color:var(--red);padding-top:14px}
.quote-text{position:absolute;left:360px;top:162px;width:480px;text-align:center;font-style:italic;font-size:14.5px;line-height:24px;color:var(--white)}
.quote-name{position:absolute;left:0;width:1200px;top:268px;text-align:center;font-weight:600;font-size:18px;color:var(--white)}
.arrow{position:absolute;top:198px}

/* Blog */
.blog-card{position:absolute;top:2247px;width:472px;height:415px;background:var(--white);box-shadow:0 4px 14px rgba(0,0,0,.12)}
.blog-photo{width:472px;height:227px}
.blog-card h3{position:absolute;left:30px;top:248px;font-family:"Nunito Sans",sans-serif;font-weight:600;font-size:21px;color:var(--red)}
.blog-card p{position:absolute;left:30px;top:286px;width:410px;font-size:13px;line-height:21px;color:var(--muted)}
.read-more{position:absolute;left:30px;top:350px;font-size:13px;font-weight:600;color:var(--ink)}

/* Apply */
.apply{position:absolute;left:0;top:2750px;width:1200px;height:413px;background:linear-gradient(180deg,#b9c8d6 0%,#cdd6de 40%,#a7b3bf 70%,#6f7f8e 100%)}
.apply h2{position:absolute;left:0;width:1200px;top:78px;text-align:center;font-family:"Nunito Sans",sans-serif;font-weight:400;font-size:40px;color:var(--white)}
.apply p{position:absolute;left:180px;width:840px;text-align:center;font-size:16px;line-height:26px;color:var(--white)}

/* Footer */
.site-footer{position:absolute;left:0;top:3163px;width:1200px;height:366px;background:var(--footer)}
.foot-col h4{position:absolute;font-family:"Nunito Sans",sans-serif;font-weight:400;font-size:20px;color:#444}
.foot-col a{position:absolute;font-size:14px;color:#555;text-decoration:none}
.social{position:absolute;left:884px;top:65px;display:flex;gap:11px}
.social span{width:38px;height:38px;border-radius:50%;background:#555}
.foot-rule{position:absolute;left:118px;top:302px;width:964px;height:1px;background:var(--line)}
.copyright{position:absolute;left:0;width:1200px;top:328px;text-align:center;font-size:12px;color:#777}
</style>
</head>
<body>

<header class="site-header">
  <div class="brand"><span class="brand-dot"></span>Bright Lantern Post</div>
  <div class="nav-marker"></div>
  <nav class="main-nav">
    <a class="active" style="left:423px">HOME</a>
    <a style="left:519px">ABOUT US</a>
    <a style="left:650px">AVAILABLE JOBS</a>
    <a style="left:833px">APPLY</a>
    <a style="left:930px">BLOG</a>
    <a style="left:1022px">FAQ</a>
  </nav>
</header>

<section class="hero" role="img" aria-label="Photo of a Chinese temple at dusk decorated with rows of glowing red lanterns">
  <h1 class="hero-title"><span class="l1">Recruit Native English</span><span class="l2">Speakers from the US &amp; UK</span></h1>
  <div class="btn-red" style="left:104px;top:349px;width:170px;height:43px;font-size:15px;font-weight:600">Learn More</div>
  <div class="hero-dots"><span class="on"></span><span></span><span class="on"></span><span class="on"></span></div>
</section>

<section class="what-we-do">
  <svg class="abs" style="left:480px;top:0" width="720" height="453" viewBox="0 0 720 453" role="img" aria-label="Photo of students in purple shirts doing a forward stretch exercise">
    <defs><linearGradient id="wwdPhoto" x1="0" y1="0" x2="1" y2="1"><stop offset="0" stop-color="#6b4a8a"/><stop offset=".5" stop-color="#8a6a7a"/><stop offset="1" stop-color="#9a8a7a"/></linearGradient></defs>
    <polygon points="296,0 720,0 720,453 6,453" fill="url(#wwdPhoto)"/>
  </svg>
  <h2 class="section-title abs" style="left:127px;top:60px">What We Do</h2>
  <p class="body-copy abs" style="left:127px;top:121px;width:450px">Want to teach English in China? Do you enjoy teaching children or adults? Would you like the adventure of teaching in China for a year?&nbsp; Then we have the perfect job for you!</p>
  <p class="body-copy abs" style="left:127px;top:210px;width:450px">We are seeking English speakers from the US, UK, Canada, Ireland, Australia, New Zealand and South Africa to teach English in China for a year (or longer if you wish).</p>
  <div class="btn-red btn-tab" style="left:125px;top:311px;width:182px;height:45px;padding-right:24px">Learn More</div>
</section>

<article class="card" style="left:118px">
  <div class="card-photo" role="img" aria-label="Photo of young children and a teacher working at a classroom table" style="background:linear-gradient(135deg,#c23a2e,#e6d2b8 55%,#8a5a3a)"></div>
  <h3>What We Offers</h3>
  <p>Competitive compensation: 8000-18,000 RMB/month, up to 40,000 RMB per month if you have a teaching license to teach in your country's public schools</p>
  <div class="btn-small">LEARN MORE</div>
</article>
<article class="card" style="left:451px">
  <div class="card-photo" role="img" aria-label="Photo of a giant carved stone Buddha statue among green trees" style="background:linear-gradient(135deg,#3e5a2e,#8a6a4e 55%,#5a4a3a)"></div>
  <h3>Teaching in China</h3>
  <p>We are seeking English speakers from the US, UK, Canada, Ireland, Australia, New Zealand and South Africa to teach English in China for a year</p>
  <div class="btn-small">LEARN MORE</div>
</article>
<article class="card" style="left:781px">
  <div class="card-photo" role="img" aria-label="Photo of Chinese schoolchildren in uniforms with red scarves" style="background:linear-gradient(135deg,#e8e4e0,#c83a3a 50%,#3a5a8a)"></div>
  <h3>English Speakers</h3>
  <p>Competitive compensation: 8000-18,000 RMB/month, up to 40,000 RMB per month if you have a teaching license to teach in your country's public schools</p>
  <div class="btn-small">LEARN MORE</div>
</article>

<section class="testimonials">
  <h2>Testimonials</h2>
  <div class="quote-pill"></div>
  <div class="quote-badge">&ldquo;</div>
  <svg class="arrow" style="left:210px" width="28" height="56" viewBox="0 0 28 56"><polyline points="24,2 4,28 24,54" fill="none" stroke="#fff" stroke-width="2"/></svg>
  <svg class="arrow" style="left:925px" width="28" height="56" viewBox="0 0 28 56"><polyline points="4,2 24,28 4,54" fill="none" stroke="#fff" stroke-width="2"/></svg>
  <p class="quote-text">As soon as we got in touch, Marissa guided me through every step of the process. I have had THE BEST experience under her guidance. Marissa has been amazing at finding the best jobs out there. I would not hesitate to recommend her to anyone!</p>
  <div class="quote-name">Clara Whitfield</div>
</section>

<h2 class="section-title abs" style="left:120px;top:2175px;font-size:32px">Our Blog Post</h2>
<article class="blog-card" style="left:118px">
  <div class="blog-photo" role="img" aria-label="Photo of a young girl having flowers painted on her cheek" style="background:linear-gradient(135deg,#7a2a2a,#d8a88a 50%,#b83a5a)"></div>
  <h3>Basic Chinese Greetings</h3>
  <p>Chinese is a pretty difficult language for English speakers to learn compared to Spanish or French. However, if you're going to China, take the time to learn some basics.</p>
  <div class="read-more">READ MORE</div>
</article>
<article class="blog-card" style="left:625px">
  <div class="blog-photo" role="img" aria-label="Photo of kindergarten children in yellow jackets outdoors" style="background:linear-gradient(135deg,#6a7a5a,#e8c83a 50%,#d8b82a)"></div>
  <h3>What are ESOL, EFL, ESL, ESP, and EAP?</h3>
  <p>Even some English language teachers don't understand the differences between these acronyms so don't feel bad if they confuse you too.</p>
  <div class="read-more">READ MORE</div>
</article>

<section class="apply" role="img" aria-label="Photo of the Shanghai skyline with its tall TV tower under a pale sky">
  <h2>Want to Apply Now</h2>
  <p style="top:146px">Please make sure you read our FREQUENTLY ASKED QUESTIONS before submitting your information. For example, the FAQ page explains that you must buy your own plane ticket to China (around $600) but most schools will reimburse you at the end of your one-year contract.</p>
  <p style="top:236px">Also, if you are black we highly suggest you first watch this video about racism in China.</p>
  <div class="btn-red btn-tab" style="left:519px;top:299px;width:173px;height:41px;padding-right:18px;font-size:15px">Click Here</div>
</section>

<footer class="site-footer">
  <div class="brand" style="top:80px;font-size:20px"><span class="brand-dot"></span>Bright Lantern Post</div>
  <div class="foot-col">
    <h4 style="left:349px;top:65px">Quick Links</h4>
    <a style="left:352px;top:107px">Home</a>
    <a style="left:352px;top:137px">About Us</a>
    <a style="left:352px;top:167px">Available Jobs</a>
    <a style="left:352px;top:197px">Why We Are</a>
  </div>
  <div class="foot-col">
    <h4 style="left:549px;top:65px">Resources</h4>
    <a style="left:553px;top:107px">Apply Now</a>
    <a style="left:553px;top:137px">Blogs</a>
    <a style="left:553px;top:167px">FAQ</a>
  </div>
  <div class="foot-col">
    <h4 style="left:724px;top:65px">Support</h4>
    <a style="left:728px;top:107px">Term of Use</a>
    <a style="left:728px;top:137px">Contact Us</a>
  </div>
  <div class="social" aria-label="Social links"><span></span><span></span><span></span><span></span></div>
  <div class="foot-rule"></div>
  <div class="copyright">© 2017 Company Name&nbsp; All right reserved&nbsp; Term of Use</div>
</footer>

</body>
</html>
```